Need Help having my business card stand out

I am the owner of Birchway Canine Training and would like for my business cards to stand out. I have been trying to keep designing them myself but I can't get what I have in my head on the card. I will try my best to post templates that I like for inspirations. I want something unique but elegant. I don't want in to look cartoony or cheesy. It needs to pop in a pet shop but also in a coffee shop or gym.

Target Market(s)

Dog owners, Married ,No young kids Jr High school kids and up (maybe kids on the way) Executives, Stay at home moms/wives, Small business owners

Industry/Entity Type

Dog Training

Contact Information for Business Card

Lowell Spratt, 281-904-3376, info@birchwaycanine.example, www.birchwaycanine.example

Colors

Designer to choose colors to be used in the design.

Requirements
Must have
• my logo
Should not have
• Cursive lettering

```html
<!DOCTYPE html>
<html lang="en">
<head>
<meta charset="utf-8">
<title>Birchway Canine Training – Business Card</title>
<link href="https://fonts.googleapis.com/css2?family=Open+Sans:wght@400;600;700&display=swap" rel="stylesheet">
<style>
  :root {
    --canvas: #b9b8b5;
    --ink: #0d0d0d;
    --charcoal: #2b2b2b;
    --silver: #c9c9c9;
    --paper: #ffffff;
    --muted: #5a5a5a;
    --url: #4a4a4a;
  }
  * { margin: 0; padding: 0; box-sizing: border-box; }
  html, body {
    width: 1200px; height: 856px; overflow: hidden;
    background: var(--canvas);
    font-family: "Open Sans", Arial, sans-serif;
  }
  .stage {
    position: relative; width: 1200px; height: 856px;
    display: flex; align-items: center; justify-content: center; gap: 40px;
  }
  .card {
    position: relative; width: 540px; height: 310px;
    border-radius: 26px; overflow: hidden;
    box-shadow: 0 10px 28px rgba(0,0,0,.25);
  }
  .card svg.art { position: absolute; inset: 0; width: 100%; height: 100%; }

  /* front */
  .brand {
    position: absolute; display: flex; align-items: center; gap: 10px;
    font-weight: 700; letter-spacing: .01em;
  }
  .card-front .brand { left: 150px; top: 58px; color: var(--ink); font-size: 19px; line-height: 1.15; }
  .brand-dot { width: 14px; height: 14px; border-radius: 50%; background: currentColor; flex: none; }
  .contact-list { position: absolute; left: 282px; top: 132px; list-style: none; }
  .contact-list li {
    display: flex; align-items: flex-start; gap: 10px;
    font-size: 12.5px; color: var(--muted); line-height: 1.45; margin-bottom: 6px;
  }
  .contact-list svg { width: 16px; height: 16px; flex: none; margin-top: 1px; }
  .holder { position: absolute; left: 30px; bottom: 30px; color: var(--paper); }
  .holder-name { font-size: 21px; font-weight: 700; }
  .holder-title { font-size: 13px; font-weight: 400; margin-top: 2px; }

  /* back */
  .card-back .brand { right: 40px; top: 70px; color: #161616; font-size: 20px; flex-direction: row; }
  .back-url { position: absolute; left: 34px; bottom: 26px; font-size: 13px; font-weight: 700; color: var(--url); }
</style>
</head>
<body>
<main class="stage">

  <section class="card card-front" aria-label="Business card front">
    <svg class="art" viewBox="0 0 540 310" preserveAspectRatio="none" aria-hidden="true">
      <defs>
        <linearGradient id="frontBlack" x1="0" y1="0" x2="1" y2="1">
          <stop offset="0" stop-color="#2a2a2a"/><stop offset="1" stop-color="#050505"/>
        </linearGradient>
        <linearGradient id="frontSilver" x1="0" y1="0" x2="1" y2="0">
          <stop offset="0" stop-color="#a9a9a9"/><stop offset="1" stop-color="#e6e6e6"/>
        </linearGradient>
      </defs>
      <rect width="540" height="310" fill="var(--paper)"/>
      <path d="M340,0 C430,20 500,60 540,110 L540,0 Z" fill="url(#frontBlack)"/>
      <path d="M110,0 C150,90 300,180 540,235 L540,250 C290,210 120,170 0,150 L0,120 C40,70 80,30 110,0 Z" fill="url(#frontSilver)" opacity=".9"/>
      <path d="M110,0 C170,100 330,190 540,245 L540,310 L0,310 L0,0 Z" fill="none"/>
      <path d="M0,130 C100,150 230,190 330,250 C380,280 440,300 540,300 L540,310 L0,310 Z" fill="var(--paper)"/>
      <path d="M0,140 C110,150 200,200 280,250 C330,285 380,304 430,310 L0,310 Z" fill="url(#frontBlack)"/>
    </svg>

    <div class="brand"><span class="brand-dot"></span><span>Birchway Canine<br>Training</span></div>

    <ul class="contact-list">
      <li>
        <svg viewBox="0 0 16 16" aria-hidden="true"><circle cx="8" cy="8" r="8" fill="#333"/><path d="M8 3.5a3 3 0 0 0-3 3c0 2.2 3 5.5 3 5.5s3-3.3 3-5.5a3 3 0 0 0-3-3z" fill="#fff"/><circle cx="8" cy="6.5" r="1.1" fill="#333"/></svg>
        <span>#000 Example Street, Alder Park,<br>Victoria, 0000, Australia</span>
      </li>
      <li>
        <svg viewBox="0 0 16 16" aria-hidden="true"><circle cx="8" cy="8" r="8" fill="#333"/><path d="M5.2 4.2l1.4-.4 1 2-1 .8c.5 1.1 1.3 1.9 2.4 2.4l.8-1 2 1-.4 1.4c-3.4.3-6.5-2.8-6.2-6.2z" fill="#fff"/></svg>
        <span>281-904-3376</span>
      </li>
      <li>
        <svg viewBox="0 0 16 16" aria-hidden="true"><circle cx="8" cy="8" r="8" fill="#333"/><rect x="4" y="5" width="8" height="6" rx=".6" fill="#fff"/><path d="M4.3 5.4L8 8.3l3.7-2.9" fill="none" stroke="#333" stroke-width=".9"/></svg>
        <span>info@birchwaycanine.example</span>
      </li>
      <li>
        <svg viewBox="0 0 16 16" aria-hidden="true"><circle cx="8" cy="8" r="8" fill="#333"/><g fill="none" stroke="#fff" stroke-width=".9"><circle cx="8" cy="8" r="4"/><ellipse cx="8" cy="8" rx="1.7" ry="4"/><path d="M4 8h8"/></g></svg>
        <span>www.birchwaycanine.example</span>
      </li>
    </ul>

    <div class="holder">
      <p class="holder-name">Lowell Spratt</p>
      <p class="holder-title">Founder</p>
    </div>
  </section>

  <section class="card card-back" aria-label="Business card back">
    <svg class="art" viewBox="0 0 540 310" preserveAspectRatio="none" aria-hidden="true">
      <defs>
        <linearGradient id="backDark" x1="0" y1="0" x2="1" y2="1">
          <stop offset="0" stop-color="#4a4a4a"/><stop offset="1" stop-color="#1f1f1f"/>
        </linearGradient>
        <linearGradient id="backLight" x1="0" y1="0" x2="1" y2="1">
          <stop offset="0" stop-color="#e4e4e4"/><stop offset="1" stop-color="#bdbdbd"/>
        </linearGradient>
      </defs>
      <rect width="540" height="310" fill="url(#backDark)"/>
      <path d="M0,80 C110,70 250,120 340,240 C360,265 372,290 380,310 L0,310 Z" fill="#0b0b0b"/>
      <path d="M0,92 C110,86 240,130 325,245 C343,270 355,292 362,310 L0,310 Z" fill="url(#backLight)"/>
    </svg>
    <div class="brand"><span class="brand-dot"></span><span>Birchway Canine Training</span></div>
    <p class="back-url">www.birchwaycanine.example</p>
  </section>

</main>
</body>
</html>
```